Psychiatric Office Needs a Website- 1st Time Ever!

Been in practice since 2003 with no website, but finally ready to dive in. We are Maplecrest Behavioral Healthcare, a mental health outpatient practice based in Fayetteville, Georgia that sees diverse individuals and families from childhood to advanced age for a variety of conditions. We've grown by word of mouth and referral but would now like to have a digital footprint. Be the pioneer of our website and we will be sure to share. We would like to see designs that are modern, animated, fairly colorful, easy to read, and caters to all ages. Also, we would like the design to take the whole page (not be centered) and can be viewed well on phone/tablet. Please see our outline for more information. Our motto/slogan is: Maplecrest Behavioral Healthcare- A step forward in your wellness journey, so the design should try to reflect that.
Updates

Project Deadline Extended
Reason: site in progress

Target Market(s)

Children through elderly

Industry/Entity Type

Medical

Logo Text

Stepping forward in your wellness journey

Number of Pages Required

1 page

Colors

Designer to choose colors to be used in the design.

Requirements
Must have
• Animation or moving pictures.
• Color.
• Concise.
• User friendly
• Diversity in the stock photos

```html
<!DOCTYPE html>
<html lang="en">
<head>
<meta charset="utf-8">
<title>Maplecrest Behavioral Healthcare</title>
<link href="https://fonts.googleapis.com/css2?family=Lobster+Two:ital,wght@0,400;0,700;1,400&family=Open+Sans:wght@400;600;700&display=swap" rel="stylesheet">
<style>
:root{
  --blue:#2a8ccc;
  --blue-dark:#1f6fa8;
  --teal:#2bbcd4;
  --green:#6aab3e;
  --green-dark:#5a9433;
  --ink:#222;
  --muted:#666;
  --line:#dcdcdc;
  --paper:#fff;
  --gray-bg:#f2f3f4;
  --footer:#7fae55;
}
*{box-sizing:border-box;margin:0;padding:0}
html,body{width:1200px;height:4337px;overflow:hidden}
body{font-family:"Open Sans",Arial,sans-serif;color:var(--ink);background:var(--paper);position:relative;font-size:13px}
.abs{position:absolute}
.script{font-family:"Lobster Two","Georgia",cursive}
.btn{display:inline-block;border-radius:30px;background:var(--green);color:#fff;font-weight:700;font-size:14px;text-transform:uppercase;text-align:center}

/* header */
.topbar{left:760px;top:0;width:440px;height:50px;background:var(--blue);color:#fff;font-size:14px;font-weight:700;display:flex;align-items:center;padding-left:60px;gap:12px;border-bottom-left-radius:30px}
.brand{left:100px;top:30px;display:flex;align-items:center;gap:14px}
.brand-mark{width:58px;height:58px;border-radius:50%;background:var(--teal)}
.brand-name{font-size:19px;font-weight:700;color:var(--blue-dark);width:220px;line-height:1.25}
.phone{left:690px;top:80px;display:flex;align-items:center;gap:10px;font-size:15px;font-weight:700;color:var(--ink)}
.phone b{color:var(--green)}
.portal{left:930px;top:74px;width:170px;height:42px;line-height:42px;font-size:13px}
.nav{left:450px;top:135px;width:650px;display:flex;justify-content:space-between;font-size:13px;color:var(--ink)}

/* hero */
.hero{left:0;top:182px;width:1200px;height:540px;background:linear-gradient(100deg,#8fa38a 0%,#c8d6b9 40%,#e6d9b4 70%,#a9b98f 100%)}
.hero-title{left:120px;top:378px;font-family:"Lobster Two",Georgia,cursive;font-size:40px;color:#fff}
.hero-sub{left:120px;top:440px;font-size:22px;color:#fff}
.hero-cta{left:120px;top:510px;width:190px;height:46px;line-height:46px}
.arrow{top:450px;width:20px;height:30px}

/* about */
.about-title{left:100px;top:835px;font-size:34px;color:var(--ink)}
.about-name{left:100px;top:880px;font-size:27px;color:var(--blue)}
.about-text{left:100px;top:930px;width:600px;font-size:13px;color:var(--muted);line-height:2.2}
.about-more{left:100px;top:1188px;width:160px;height:46px;line-height:46px}
.form{left:725px;top:835px;width:375px;height:405px;border:1px solid var(--line);box-shadow:0 0 10px rgba(0,0,0,.08);padding:28px 30px}
.form h3{text-align:center;font-size:22px;font-weight:600;margin-bottom:22px;letter-spacing:.5px}
.field{border:1px solid var(--line);height:40px;font-size:12px;color:#999;padding:11px 12px;margin-bottom:12px}
.row{display:flex;gap:12px}.row .field{flex:1}
.field.tall{height:78px}
.submit{background:var(--blue);color:#fff;text-align:center;font-weight:700;height:40px;line-height:40px}

/* services */
.services{left:0;top:1330px;width:1200px;height:910px;background:var(--gray-bg)}
.sec-title{width:1200px;left:0;text-align:center;font-family:"Lobster Two",Georgia,cursive;font-size:42px;color:var(--ink)}
.sec-title span{color:var(--blue)}
.card{width:335px;background:#fff;box-shadow:0 0 8px rgba(0,0,0,.1)}
.card .photo{height:185px}
.card .label{height:95px;display:flex;align-items:center;justify-content:center;text-align:center;font-size:15px;font-weight:600;padding:0 16px;line-height:1.5}
.card .label small{font-size:11px;font-weight:400}
.all-btn{left:490px;top:2092px;width:220px;height:46px;line-height:46px}

/* conditions */
.cond{top:2420px;width:190px;text-align:center;font-size:15px;color:var(--ink)}
.cond svg{display:block;margin:0 auto 18px}

/* faq */
.faq-photo{left:0;top:2730px;width:1200px;height:440px;background:linear-gradient(120deg,#e9eef2 0%,#c9d6df 45%,#2a8ccc 46%,#1e77b8 100%)}
.faq-title{left:660px;top:2770px;font-size:31px;color:#fff}
.faq-list{left:660px;top:2830px;width:440px}
.faq-item{height:38px;margin-bottom:8px;background:var(--teal);color:#fff;font-size:13px;font-weight:600;display:flex;justify-content:space-between;align-items:center;padding:0 14px}
.faq-item.open{background:#fff;color:var(--ink);font-weight:400}
.faq-more{left:1040px;top:3105px;color:#fff;font-size:12px;text-decoration:underline}

/* news */
.news{top:3290px;width:320px;background:#fff;box-shadow:0 0 8px rgba(0,0,0,.1)}
.news .photo{height:200px}
.news h4{text-align:center;font-size:15px;font-weight:700;margin-top:25px}
.news p{text-align:center;font-size:12px;color:var(--muted);margin:12px 22px;line-height:1.6}
.news .meta{border-top:1px solid var(--line);margin:20px 0 0;padding:14px 0;text-align:center;font-size:12px;color:var(--blue)}

/* footer */
.footer{left:0;top:3780px;width:1200px;height:557px;background:linear-gradient(180deg,#8cba5f,#6f9f45)}
.fcol{top:3950px;color:#fff}
.fcol h5{font-size:17px;font-weight:600;margin-bottom:28px;letter-spacing:.5px}
.fcol li{list-style:none;font-size:13px;margin-bottom:14px;display:flex;gap:12px;align-items:center}
.dot{width:12px;height:12px;border-radius:50%;background:#fff;flex:none}
.copy{left:0;top:4275px;width:1200px;text-align:center;color:#fff;font-size:13px;border-top:1px solid rgba(255,255,255,.4);padding-top:18px}
</style>
</head>
<body>

<div class="abs topbar"><svg width="22" height="22" viewBox="0 0 22 22"><circle cx="11" cy="11" r="9" fill="none" stroke="#fff" stroke-width="2"/><path d="M11 6v5l4 2" stroke="#fff" stroke-width="2" fill="none"/></svg>OPENING HOURS : MON - SAT : 8.00 - 18.00</div>
<div class="abs brand"><div class="brand-mark"></div><div class="brand-name">Maplecrest Behavioral Healthcare</div></div>
<div class="abs phone"><svg width="28" height="28" viewBox="0 0 24 24"><path d="M6.6 10.8a15 15 0 0 0 6.6 6.6l2.2-2.2c.3-.3.7-.4 1-.2 1.1.4 2.3.6 3.6.6.6 0 1 .4 1 1V20c0 .6-.4 1-1 1A17 17 0 0 1 3 4c0-.6.4-1 1-1h3.5c.6 0 1 .4 1 1 0 1.3.2 2.5.6 3.6.1.3 0 .7-.2 1z" fill="var(--blue)"/></svg><span><b>PHONE</b> : (770) - 555 - 0142</span></div>
<div class="abs btn portal">Patient Portal</div>
<nav class="abs nav"><span>HOME</span><span>ABOUT US</span><span>SERVICES</span><span>CONDITIONS WE TREAT</span><span>NEW PATIENTS</span><span>CONTACT US</span></nav>

<div class="abs hero" role="img" aria-label="Photo of a smiling grandfather carrying a young boy on his shoulders outdoors"></div>
<svg class="abs" style="left:0;top:640px" width="1200" height="90" viewBox="0 0 1200 90" preserveAspectRatio="none"><path d="M0 30 C300 110 700 0 1200 20 V90 H0Z" fill="var(--teal)"/><path d="M0 55 C350 120 750 20 1200 40 V90 H0Z" fill="var(--blue)"/><path d="M0 70 C350 120 800 40 1200 55 V90 H0Z" fill="#fff"/></svg>
<svg class="abs arrow" style="left:40px" viewBox="0 0 20 30"><path d="M16 2 4 15l12 13" stroke="#fff" stroke-width="3" fill="none"/></svg>
<svg class="abs arrow" style="left:1140px" viewBox="0 0 20 30"><path d="M4 2l12 13L4 28" stroke="#fff" stroke-width="3" fill="none"/></svg>
<div class="abs hero-title">Maplecrest Behavioral Healthcare</div>
<div class="abs hero-sub">A step forward in your wellness journey</div>
<div class="abs btn hero-cta">Take a screening</div>

<div class="abs about-title script">About</div>
<div class="abs about-name script">Maplecrest Behavioral Healthcare</div>
<p class="abs about-text">To be the leading provider of outpatient psychiatric care in Atlanta Metro South, working together to promote (the) mental wellness of our community.<br>To provide mental health services to children, adults, and the developmentally disabled population that is culturally sensitive regardless of age, race, gender, orientation, religion, or creed; To work hand in hand with clients to overcome mental health challenges and improve their quality of life To partner with families and caregivers in achieving desired treatment goals for the client.</p>
<div class="abs btn about-more">Read More</div>
<form class="abs form">
  <h3>APPOINTMENT FORM</h3>
  <div class="field">Your Name</div>
  <div class="row"><div class="field">Email</div><div class="field">Phone</div></div>
  <div class="row"><div class="field">Day</div><div class="field">Time</div></div>
  <div class="field tall">Your Message</div>
  <div class="submit">SUBMIT</div>
</form>

<div class="abs services"></div>
<h2 class="abs sec-title" style="top:1395px">Our <span>Services</span></h2>
<div class="abs card" style="left:100px;top:1485px"><div class="photo" role="img" aria-label="Photo of a clinician checking a patient's blood pressure" style="background:linear-gradient(135deg,#a57a5a,#d9c3a9)"></div><div class="label">DIAGNOSTIC EVALUATION AND TREATMENT</div></div>
<div class="abs card" style="left:442px;top:1485px"><div class="photo" role="img" aria-label="Photo of a bright consultation office" style="background:linear-gradient(135deg,#e6e6e6,#bfc8cc)"></div><div class="label">PSYCHOPHARMACOLOGY</div></div>
<div class="abs card" style="left:785px;top:1485px"><div class="photo" role="img" aria-label="Photo of a body fat caliper measurement" style="background:linear-gradient(135deg,#d7b49a,#f0e0d0)"></div><div class="label">BARIATRIC PRE-SURGICAL CONSULTATION <small>&nbsp;(and other surgeries)</small></div></div>
<div class="abs card" style="left:100px;top:1785px"><div class="photo" role="img" aria-label="Photo of a thoughtful young woman" style="background:linear-gradient(135deg,#3c5a7a,#8aa0b8)"></div><div class="label">DISABILITY AND WORK-RELATED REPORTS <small>&nbsp;(include?)</small></div></div>
<div class="abs card" style="left:442px;top:1785px"><div class="photo" role="img" aria-label="Photo of a mother with a young child" style="background:linear-gradient(135deg,#c9a78a,#efe3d6)"></div><div class="label">EARLY CHILDHOOD ASSESSMENTS</div></div>
<div class="abs card" style="left:785px;top:1785px"><div class="photo" role="img" aria-label="Photo of a caregiver assisting an older woman" style="background:linear-gradient(135deg,#b39a84,#e8ddd2)"></div><div class="label">SUBSTANCE ABUSE ASSESSMENTS</div></div>
<div class="abs btn all-btn">View all services</div>

<h2 class="abs sec-title" style="top:2310px">Conditions <span>We Treat</span></h2>
<div class="abs cond" style="left:70px"><svg width="160" height="160" viewBox="0 0 160 160"><circle cx="80" cy="80" r="72" fill="none" stroke="var(--teal)" stroke-width="6"/><circle cx="80" cy="80" r="58" fill="none" stroke="var(--teal)" stroke-width="2"/><circle cx="80" cy="80" r="26" fill="none" stroke="var(--blue)" stroke-width="4"/></svg>Mood Disorders</div>
<div class="abs cond" style="left:270px"><svg width="160" height="160" viewBox="0 0 160 160"><circle cx="80" cy="80" r="72" fill="none" stroke="var(--teal)" stroke-width="6"/><circle cx="80" cy="80" r="58" fill="none" stroke="var(--teal)" stroke-width="2"/><rect x="58" y="58" width="44" height="44" rx="8" fill="none" stroke="var(--blue)" stroke-width="4"/></svg>Anxiety Disorders</div>
<div class="abs cond" style="left:495px;top:2405px"><svg width="200" height="200" viewBox="0 0 200 200"><circle cx="100" cy="100" r="92" fill="none" stroke="var(--teal)" stroke-width="7"/><circle cx="100" cy="100" r="75" fill="none" stroke="var(--teal)" stroke-width="2"/><path d="M100 60c-14 0-16 22 0 44l-22 34M100 104l22 34" stroke="var(--teal)" stroke-width="9" fill="none" stroke-linecap="round"/></svg>Common Disorders of<br>Childhood</div>
<div class="abs cond" style="left:735px"><svg width="160" height="160" viewBox="0 0 160 160"><circle cx="80" cy="80" r="72" fill="none" stroke="var(--teal)" stroke-width="6"/><circle cx="80" cy="80" r="58" fill="none" stroke="var(--teal)" stroke-width="2"/><circle cx="80" cy="80" r="26" fill="var(--blue)"/></svg>Psychotic Disorders</div>
<div class="abs cond" style="left:935px"><svg width="160" height="160" viewBox="0 0 160 160"><circle cx="80" cy="80" r="72" fill="none" stroke="var(--teal)" stroke-width="6"/><circle cx="80" cy="80" r="58" fill="none" stroke="var(--teal)" stroke-width="2"/><circle cx="80" cy="80" r="24" fill="none" stroke="var(--blue)" stroke-width="4"/><path d="M66 80h28" stroke="var(--blue)" stroke-width="4"/></svg>Eating Disorders</div>

<div class="abs faq-photo" role="img" aria-label="Photo of a doctor's coat and stethoscope"></div>
<div class="abs faq-title script">Frequently Asked Questions</div>
<div class="abs faq-list">
  <div class="faq-item">What do I need to bring with me to my first visit? <span>+</span></div>
  <div class="faq-item open">Insurance card, patient forms found on our Form's page.</div>
  <div class="faq-item">How long do I have to wait to be seen? <span>+</span></div>
  <div class="faq-item">What type of insurance do you accept? <span>+</span></div>
  <div class="faq-item">Why is my child not doing well in school? <span>+</span></div>
  <div class="faq-item">I feel sad/tired and I do not have energy is that normal? <span>+</span></div>
</div>
<div class="abs faq-more">View All &gt;&gt;</div>

<h2 class="abs sec-title" style="top:3215px">Latest <span>News &amp; Tips</span></h2>
<div class="abs news" style="left:100px"><div class="photo" role="img" aria-label="Photo of a person reaching out a hand" style="background:linear-gradient(135deg,#8e8e8e,#d6d6d6)"></div><h4>CIRCUMSTANCES OCCUR INOILA</h4><p>Sed ut perspiciatis unde omnis iste natus error sit voluptatem accusantium doloremque</p><div class="meta">March 12,2017 &nbsp;|&nbsp; 6 comments &nbsp;|&nbsp; 3</div></div>
<div class="abs news" style="left:440px"><div class="photo" role="img" aria-label="Photo of a doctor speaking with a patient" style="background:linear-gradient(135deg,#b9c9d6,#eef2f5)"></div><h4>SED QUIA NON NUMQUAM EIUS</h4><p>Sed ut perspiciatis unde omnis iste natus error sit voluptatem accusantium doloremque</p><div class="meta">March 12,2017 &nbsp;|&nbsp; 6 comments &nbsp;|&nbsp; 3</div></div>
<div class="abs news" style="left:780px"><div class="photo" role="img" aria-label="Photo of a counselor meeting a client" style="background:linear-gradient(135deg,#a38a72,#e3d6c8)"></div><h4>QUIS NOSTRUD EXERULLAMCO</h4><p>Sed ut perspiciatis unde omnis iste natus error sit voluptatem accusantium doloremque</p><div class="meta">March 12,2017 &nbsp;|&nbsp; 6 comments &nbsp;|&nbsp; 3</div></div>

<div class="abs footer" role="img" aria-label="Soft green photo of a family outdoors behind the footer"></div>
<svg class="abs" style="left:0;top:3740px" width="1200" height="90" viewBox="0 0 1200 90" preserveAspectRatio="none"><path d="M0 40 C400 0 800 60 1200 10 V90 H0Z" fill="var(--teal)"/><path d="M0 55 C400 20 800 75 1200 30 V90 H0Z" fill="#8cba5f"/></svg>
<div class="abs fcol" style="left:100px"><h5>CONTACT US</h5><ul>
  <li><span class="dot"></span>1716 Willow Bend Road, Fayetteville</li>
  <li><span class="dot"></span>Call Us : (770) - 555 - 0142</li>
  <li><span class="dot"></span>Hours : Mon-Sat (8.00 to 18.00)</li>
  <li><span class="dot"></span>hello@maplecrestbh.com</li></ul></div>
<div class="abs fcol" style="left:410px"><h5>QUICK LINKS</h5><ul>
  <li>› Home</li><li>› About Us</li><li>› Services</li><li>› Conditions We Treat</li><li>› New Patients</li><li>› Contact Us</li></ul></div>
<div class="abs fcol" style="left:630px;width:280px"><h5>SIGN UP NEWSLETTER</h5>
  <p style="font-size:12px;line-height:1.6;margin-bottom:14px">Get wellness tips, clinic news and event updates sent straight to your inbox.</p>
  <div style="background:#fff;color:#999;height:38px;padding:10px;font-size:12px">Enter email...</div>
  <div style="background:var(--blue);color:#fff;width:100px;height:32px;line-height:32px;text-align:center;font-size:12px;margin-top:12px;font-weight:700">SUBSCRIBE</div></div>
<div class="abs fcol" style="left:975px"><h5>FOLLOW US</h5><ul><li><span style="width:36px;height:36px;border:2px solid #fff;border-radius:50%;display:inline-block"></span>Connect</li></ul></div>
<div class="abs copy">© copyright 2017 Maplecrest Behavioral Healthcare . All rights reserved &nbsp;|&nbsp; Privacy policy</div>

</body>
</html>
```